Business Card for Industrial Distributor

We need a business card design for an industrial distributor. We sell machine parts for the manufacturing and oil industry. We would like the cards to look clean and modern but with a touch of industry.

Our colors are blue/white.

Please feel free to visit our website www.korvelpartsco.com

Target Market(s)

mexican manufacturers in the automobile/aerospace industry

Industry/Entity Type

Industrial

Colors
ffffff
0555a3

```html
<!DOCTYPE html>
<html lang="en">
<head>
<meta charset="utf-8">
<title>Korvel Business Card</title>
<link href="https://fonts.googleapis.com/css2?family=Noto+Sans:wght@400;700;800&display=swap" rel="stylesheet">
<style>
  :root {
    --brand-blue: #283a8f;
    --globe-blue: #1565b8;
    --swoosh-grey: #a3a3a3;
    --text-grey: #8c8c8c;
    --card-white: #ffffff;
    --backdrop: #ece8e1;
  }
  html, body {
    margin: 0;
    padding: 0;
    width: 1200px;
    height: 1076px;
    overflow: hidden;
    background: var(--backdrop);
  }
  .canvas {
    position: relative;
    width: 1200px;
    height: 1076px;
  }
  .card {
    position: absolute;
    left: 180px;
    width: 840px;
    height: 485px;
    border-radius: 26px;
    overflow: hidden;
    background: var(--card-white);
    box-shadow: 0 6px 18px rgba(0,0,0,0.18);
  }
  .card--front { top: 33px; }
  .card--back { top: 558px; }
  .card svg { display: block; width: 100%; height: 100%; }
  .wordmark {
    font-family: "Noto Sans", sans-serif;
    font-weight: 800;
    fill: var(--brand-blue);
    letter-spacing: -2px;
  }
  .person-name {
    font-family: "Noto Sans", sans-serif;
    font-weight: 700;
    font-size: 29px;
    fill: var(--brand-blue);
  }
  .person-title, .contact-line, .address-line {
    font-family: "Noto Sans", sans-serif;
    font-weight: 400;
    fill: var(--text-grey);
  }
  .person-title { font-size: 24px; }
  .contact-line { font-size: 23px; }
  .address-line { font-size: 23px; }
  .company-name {
    font-family: "Noto Sans", sans-serif;
    font-weight: 700;
    font-size: 27px;
    fill: var(--brand-blue);
  }
  .web-address {
    font-family: "Noto Sans", sans-serif;
    font-weight: 400;
    font-size: 22px;
    fill: var(--card-white);
  }
  .icon-box { fill: var(--brand-blue); }
  .icon-mark { fill: none; stroke: var(--card-white); stroke-width: 1.6; }
</style>
</head>
<body>
<main class="canvas">

  <section class="card card--front" aria-label="Card front">
    <svg viewBox="0 0 910 525" xmlns="http://www.w3.org/2000/svg">
      <path class="band-top" fill="var(--brand-blue)" d="M0,0 H910 V60 C700,140 360,180 0,170 Z"/>
      <path class="swoosh-top" fill="var(--swoosh-grey)" d="M80,205 C420,200 700,150 910,80 V118 C700,178 420,212 80,205 Z"/>
      <circle class="brand-dot" cx="205" cy="262" r="56" fill="var(--globe-blue)"/>
      <text class="wordmark" x="300" y="300" font-size="118">Korvel</text>
      <path class="swoosh-bottom" fill="var(--swoosh-grey)" d="M0,430 C300,395 620,368 880,352 C620,385 300,430 0,485 Z"/>
      <path class="band-bottom" fill="var(--brand-blue)" d="M0,505 C300,440 620,395 910,378 V525 H0 Z"/>
    </svg>
  </section>

  <section class="card card--back" aria-label="Card back">
    <svg viewBox="0 0 910 525" xmlns="http://www.w3.org/2000/svg">
      <text class="wordmark" x="56" y="150" font-size="118">Korvel</text>

      <text x="58" y="224"><tspan class="person-name">DANIEL REYES</tspan><tspan class="person-title" dx="12">Manager</tspan></text>

      <g class="contact-list">
        <rect class="icon-box" x="58" y="259" width="24" height="24" rx="3"/>
        <path class="icon-mark" d="M64,276 h12 v-5 q-6,-5 -12,0 Z M66,266 h8"/>
        <text class="contact-line" x="89" y="280">(555) 014 - 2290</text>

        <rect class="icon-box" x="58" y="288" width="24" height="24" rx="3"/>
        <path class="icon-mark" d="M63,299 h14 v8 h-14 Z M66,299 v-5 h8 v5"/>
        <text class="contact-line" x="89" y="309">(555) 014 - 2291</text>

        <rect class="icon-box" x="58" y="318" width="24" height="24" rx="3"/>
        <path class="icon-mark" d="M62,323 h16 v13 h-16 Z M62,323 l8,7 l8,-7"/>
        <text class="contact-line" x="89" y="339">sales@korvelpartsco.com</text>
      </g>

      <g class="company-block" text-anchor="end">
        <text class="company-name" x="875" y="282">Korvel International Corp.</text>
        <text class="address-line" x="875" y="313">4180 Harbor Mill Rd.</text>
        <text class="address-line" x="875" y="344">Mesa Verde, TX 78500</text>
      </g>

      <path class="swoosh-bottom" fill="var(--swoosh-grey)" d="M0,392 C250,374 560,368 860,388 C560,382 260,404 0,455 Z"/>
      <path class="band-bottom" fill="var(--brand-blue)" d="M0,470 C260,418 580,402 910,406 V525 H0 Z"/>
      <text class="web-address" x="875" y="487" text-anchor="end">www.korvelpartsco.com</text>
    </svg>
  </section>

</main>
</body>
</html>
```